Solvera Harvest Co - Business Card Design Project

We need business cards for our business. We grow roots and fruits in Central and South America, we import and distribute in FL, USA. We do fresh and frozen products.

Target Market(s)

Small and big supermarkets, wholesalers, traders, distributors, etc

Industry/Entity Type

Business

```html
<!DOCTYPE html>
<html lang="en">
<head>
<meta charset="utf-8">
<title>Solvera Harvest Co – Business Card</title>
<link rel="stylesheet" href="https://fonts.googleapis.com/css2?family=Mulish:wght@400;600;800&display=swap">
<style>
  :root {
    --backdrop: #2b2b2b;
    --card: #ffffff;
    --orange: #e07b12;
    --leaf: #4a5e2a;
    --ink: #2e2e2e;
    --rule: #9a9a9a;
  }
  * { margin: 0; padding: 0; box-sizing: border-box; }
  html, body { width: 1200px; height: 1116px; overflow: hidden; }
  body {
    background: var(--backdrop);
    font-family: "Mulish", "Century Gothic", sans-serif;
    display: flex; align-items: center; justify-content: center;
  }
  .business-card {
    position: relative;
    width: 900px; height: 514px;
    background: var(--card);
    border-radius: 26px;
    box-shadow: 0 20px 50px rgba(0,0,0,.45);
  }
  .brand {
    position: absolute; top: 72px; right: 90px;
    display: flex; align-items: center; gap: 14px;
  }
  .brand-dot { width: 22px; height: 22px; border-radius: 50%; background: var(--leaf); }
  .brand-name {
    font-weight: 800; font-size: 40px; color: var(--leaf);
    letter-spacing: .5px; white-space: nowrap;
  }
  .brand-rule {
    position: absolute; top: 140px; right: 90px;
    width: 400px; height: 1px; background: var(--rule);
  }
  .holder { position: absolute; left: 72px; top: 286px; }
  .holder-name { font-weight: 800; font-size: 30px; color: var(--orange); letter-spacing: .5px; }
  .holder-role { font-size: 24px; color: var(--ink); margin-top: 2px; }
  .website {
    position: absolute; left: 380px; top: 322px;
    display: flex; align-items: center; gap: 12px;
    font-size: 21px; color: var(--ink); white-space: nowrap;
  }
  .contact-list {
    position: absolute; left: 72px; top: 372px;
    list-style: none; display: flex; flex-direction: column; gap: 14px;
  }
  .contact-item { display: flex; align-items: center; gap: 14px; font-size: 21px; color: var(--ink); white-space: nowrap; }
  .icon { width: 22px; height: 22px; flex: none; fill: var(--orange); }
</style>
</head>
<body>
  <article class="business-card">
    <div class="brand">
      <span class="brand-dot"></span>
      <span class="brand-name">Solvera Harvest Co</span>
    </div>
    <div class="brand-rule"></div>

    <div class="holder">
      <p class="holder-name">YOUR NAME</p>
      <p class="holder-role">Designation</p>
    </div>

    <p class="website">
      <svg class="icon" viewBox="0 0 24 24" aria-hidden="true"><path d="M10 14a4 4 0 0 1 0-6l3-3a4 4 0 0 1 6 6l-1.5 1.5-1.4-1.4L17.6 9.6a2 2 0 0 0-2.8-2.8l-3 3a2 2 0 0 0 0 2.8zM14 10a4 4 0 0 1 0 6l-3 3a4 4 0 0 1-6-6l1.5-1.5 1.4 1.4-1.5 1.5a2 2 0 0 0 2.8 2.8l3-3a2 2 0 0 0 0-2.8z"/></svg>
      www.solveraharvest.com
    </p>

    <ul class="contact-list">
      <li class="contact-item">
        <svg class="icon" viewBox="0 0 24 24" aria-hidden="true"><path d="M3 8c0-2 3-4 9-4s9 2 9 4v2h-5V8H8v2H3zM5 12h14l1 7H4zm7 1.5a2.5 2.5 0 1 0 0 5 2.5 2.5 0 0 0 0-5z"/></svg>
        +1 555-014-2290
      </li>
      <li class="contact-item">
        <svg class="icon" viewBox="0 0 24 24" aria-hidden="true"><path d="M12 3l10 9h-3v8h-5v-5h-4v5H5v-8H2z"/></svg>
        212 Orchard Lane Millbrook, Florida 33001
      </li>
      <li class="contact-item">
        <svg class="icon" viewBox="0 0 24 24" aria-hidden="true"><path d="M2 5h20v14H2zm2 2v.5l8 5.5 8-5.5V7z"/></svg>
        hello@solveraharvest.com
      </li>
    </ul>
  </article>
</body>
</html>
```